Web Design

We need a website for a company based in Doha Qatar called
Lumara Maid Service.

It is the number one maid cleaning service company, and we have branches all over qatar.

Luxury Cleaning Service Provider.

The color scheme is gold, yellow and black like the logo.

Before they get to the website, there is an intro video.

The website should depict luxury.

Target Market(s)

People who need maids at their houses.

Industry/Entity Type

Cleaning Service

Requirements
Must have
• Luxury, Sleek, Modern

The opening sequence is a video which I already have. Its too big to upload here so I am going to put it on youtube.

After the opening sequence, the home page should have a widescreen photo background and it should change every five seconds, the first background photo should be of qatar westbay skyline. Then the second background should be of maid photos in cleaning positions. Then the third background should be of cleaner photos etc.

We will send you all the tabs and all the content later.

```html
<!DOCTYPE html>
<html lang="en">
<head>
<meta charset="UTF-8">
<title>Lumara Maid Service</title>
<link href="https://fonts.googleapis.com/css2?family=Bebas+Neue&family=Open+Sans:wght@400&family=Oxygen:wght@400&display=swap" rel="stylesheet">
<style>
  :root {
    --gold: #b8862f;
    --yellow: #fff57a;
    --black: #000000;
    --white: #ffffff;
    --ink: #1a1a1a;
    --dot-idle: #e6e8ee;
    --social: #5a6f96;
    --sky-top: #4f6583;
    --sky-mid: #8394ad;
    --water: #2a3c3f;
  }
  * { margin: 0; padding: 0; box-sizing: border-box; }
  html, body { width: 1200px; height: 800px; overflow: hidden; background: var(--white); }
  body { position: relative; font-family: "Open Sans", sans-serif; }

  .site-header { position: absolute; left: 0; top: 0; width: 1200px; height: 100px; background: var(--white); }
  .brand { position: absolute; left: 100px; top: 36px; display: flex; align-items: center; gap: 10px; }
  .brand-mark { width: 18px; height: 18px; border-radius: 50%; background: var(--gold); }
  .brand-name { font-family: "Open Sans", sans-serif; font-size: 18px; color: var(--gold); letter-spacing: 0.3px; }

  .main-nav { position: absolute; top: 33px; left: 524px; display: flex; }
  .main-nav a { display: block; height: 42px; line-height: 42px; padding: 0 20px; margin-right: 15px; font-size: 14px; color: var(--ink); text-decoration: none; border-radius: 4px; }
  .main-nav a.is-active { background: var(--yellow); }

  .hero { position: absolute; left: 0; top: 100px; width: 1200px; height: 600px; overflow: hidden; }
  .hero-photo { position: absolute; inset: 0; background: linear-gradient(180deg, var(--sky-top) 0%, var(--sky-mid) 35%, #6f7c8a 62%, #4a5a5e 66%, var(--water) 100%); }
  .hero-shade { position: absolute; inset: 0; background: rgba(0,0,0,0.12); }
  .hero-title { position: absolute; left: 100px; top: 186px; font-family: "Bebas Neue", sans-serif; font-size: 50px; line-height: 56px; color: var(--yellow); letter-spacing: 0.3px; }
  .hero-text { position: absolute; left: 100px; top: 252px; width: 530px; font-size: 18px; line-height: 30px; color: var(--white); }
  .hero-cta { position: absolute; left: 100px; top: 364px; width: 134px; height: 54px; line-height: 56px; text-align: center; background: var(--yellow); color: var(--black); font-family: "Bebas Neue", sans-serif; font-size: 25px; text-decoration: none; }
  .slide-arrow { position: absolute; top: 288px; }
  .slide-arrow.prev { left: 43px; }
  .slide-arrow.next { left: 1132px; }
  .slide-dots { position: absolute; left: 1026px; top: 575px; display: flex; gap: 8px; }
  .slide-dots span { width: 13px; height: 13px; border-radius: 50%; background: var(--dot-idle); }
  .slide-dots span.is-active { background: var(--yellow); }

  .site-footer { position: absolute; left: 0; top: 700px; width: 1200px; height: 100px; background: var(--black); color: var(--white); font-family: "Oxygen", sans-serif; }
  .footer-nav { position: absolute; left: 98px; top: 24px; font-size: 17px; }
  .footer-nav a { color: var(--white); text-decoration: none; }
  .footer-nav .sep { margin: 0 8px; }
  .copyright { position: absolute; left: 98px; top: 58px; font-size: 13px; }
  .social { position: absolute; left: 978px; top: 38px; display: flex; gap: 9px; }
  .social span { width: 23px; height: 23px; border-radius: 2px; background: var(--social); }
</style>
</head>
<body>
  <header class="site-header">
    <div class="brand">
      <span class="brand-mark"></span>
      <span class="brand-name">Lumara Maid Service</span>
    </div>
    <nav class="main-nav">
      <a href="#" class="is-active">Home</a>
      <a href="#">About Us</a>
      <a href="#">Services</a>
      <a href="#">Testimonals</a>
      <a href="#">Contact Us</a>
    </nav>
  </header>

  <section class="hero">
    <div class="hero-photo" role="img" aria-label="Doha West Bay skyline of towers across the calm bay water under a blue sky"></div>
    <div class="hero-shade"></div>
    <h1 class="hero-title">LOREM IPSUM DOLOR SIT AMET</h1>
    <p class="hero-text">Nulla consequat massa quis enim. Donec pede justo, fringilla vel, aliquet nec, vulputate eget, arcu. In enim justo, rhoncus ut, imperdiet a, venenatis vitae, justo.</p>
    <a href="#" class="hero-cta">READ MORE +</a>
    <svg class="slide-arrow prev" width="26" height="40" viewBox="0 0 26 40" aria-hidden="true"><path d="M20 4 L6 20 L20 36" fill="none" stroke="#fff" stroke-width="7" stroke-linejoin="miter"/></svg>
    <svg class="slide-arrow next" width="26" height="40" viewBox="0 0 26 40" aria-hidden="true"><path d="M6 4 L20 20 L6 36" fill="none" stroke="#fff" stroke-width="7" stroke-linejoin="miter"/></svg>
    <div class="slide-dots"><span class="is-active"></span><span></span><span></span></div>
  </section>

  <footer class="site-footer">
    <nav class="footer-nav">
      <a href="#">Home</a><span class="sep">|</span><a href="#">About Us</a><span class="sep">|</span><a href="#">Services</a><span class="sep">|</span><a href="#">Products</a><span class="sep">|</span><a href="#">Contact Us</a><span class="sep">|</span><a href="#">Blog</a>
    </nav>
    <p class="copyright">© 2014 Company Name&nbsp; All right reserved&nbsp; Term of Use</p>
    <div class="social"><span></span><span></span><span></span><span></span></div>
  </footer>
</body>
</html>
```